Business Card Design

We are a commercial real estate brokerage in San Francisco, leasing office buildings downtown.
I would like a clean, elegant look. Simple but powerful .

Industry/Entity Type

Business

Contact Information for Business Card

Derek Holloway
lic# 07258143
415.555.0172
derek@velt-commercial.example
velt-commercial.example

```html
<!DOCTYPE html>
<html lang="en">
<head>
<meta charset="utf-8">
<title>Velt Commercial — Business Card</title>
<link rel="stylesheet" href="https://fonts.googleapis.com/css2?family=Source+Sans+3:wght@400;600&display=swap">
<style>
  :root {
    --backdrop: #8c8d8d;
    --paper: #e9e9eb;
    --slate-blue: #5f7699;
    --charcoal: #4a4a4c;
    --ink: #3c3c3e;
    --rule: #9a9a9c;
  }
  * { box-sizing: border-box; margin: 0; padding: 0; }
  html, body {
    width: 1105px; height: 1200px; overflow: hidden;
    background: var(--backdrop);
    font-family: "Source Sans 3", "Myriad Pro", sans-serif;
  }
  .card {
    position: absolute; left: 182px;
    width: 746px; height: 427px;
    background: var(--paper);
    overflow: hidden;
  }
  .card--front { top: 119px; }
  .card--back { top: 636px; }

  .wordmark {
    position: absolute;
    display: flex; align-items: center; gap: 18px;
    color: var(--slate-blue); font-weight: 600;
    line-height: 0.95; letter-spacing: 1px;
  }
  .wordmark__square { background: var(--slate-blue); flex: none; }
  .wordmark__name { text-transform: uppercase; }
  .card--front .wordmark { right: 45px; top: 52px; font-size: 40px; }
  .card--front .wordmark__square { width: 54px; height: 54px; }
  .card--back .wordmark { left: 50%; top: 50%; transform: translate(-50%, -50%); font-size: 52px; gap: 24px; }
  .card--back .wordmark__square { width: 72px; height: 72px; }

  .holder-name {
    position: absolute; left: 41px; top: 238px;
    font-size: 25px; font-weight: 600; letter-spacing: 0.5px;
    color: var(--slate-blue); text-transform: uppercase;
  }
  .holder-rule {
    position: absolute; left: 41px; right: 45px; top: 283px;
    height: 1px; background: var(--rule);
  }
  .contact-list {
    position: absolute; left: 41px; top: 296px;
    list-style: none;
  }
  .contact-list li {
    display: flex; align-items: center; gap: 11px;
    height: 29px; font-size: 19px; color: var(--ink);
  }
  .contact-list svg { width: 17px; height: 17px; fill: var(--charcoal); flex: none; }
  .licence {
    position: absolute; right: 45px; top: 355px;
    font-size: 19px; color: var(--ink);
  }
  .accent-band { position: absolute; left: 0; bottom: 0; width: 746px; height: 14px; }
</style>
</head>
<body>

<section class="card card--front" aria-label="Business card front">
  <div class="wordmark">
    <span class="wordmark__square"></span>
    <span class="wordmark__name">Velt<br>Commercial</span>
  </div>

  <h1 class="holder-name">Derek Holloway</h1>
  <div class="holder-rule"></div>

  <ul class="contact-list">
    <li>
      <svg viewBox="0 0 24 24" aria-hidden="true"><path d="M6.6 10.8a15.1 15.1 0 0 0 6.6 6.6l2.2-2.2a1 1 0 0 1 1-.25 11.4 11.4 0 0 0 3.6.57 1 1 0 0 1 1 1V20a1 1 0 0 1-1 1A17 17 0 0 1 3 4a1 1 0 0 1 1-1h3.5a1 1 0 0 1 1 1c0 1.25.2 2.45.57 3.57a1 1 0 0 1-.25 1z"/></svg>
      415.555.0172
    </li>
    <li>
      <svg viewBox="0 0 24 24" aria-hidden="true"><path d="M2 5h20v14H2z M3.5 6.5 12 12.5l8.5-6z" fill-rule="evenodd"/></svg>
      derek@velt-commercial.example
    </li>
    <li>
      <svg viewBox="0 0 24 24" aria-hidden="true"><path d="M12 2a10 10 0 1 0 0 20 10 10 0 0 0 0-20zm-1 17.9A8 8 0 0 1 4.2 10.8L9 15.6v1a2 2 0 0 0 2 2zm6.9-2.5A2 2 0 0 0 16 16h-1v-3a1 1 0 0 0-1-1H8v-2h2a1 1 0 0 0 1-1V7h2a2 2 0 0 0 2-2v-.4a8 8 0 0 1 2.9 12.8z"/></svg>
      velt-commercial.example
    </li>
  </ul>

  <p class="licence">lic# 07258143</p>

  <svg class="accent-band" viewBox="0 0 746 14" preserveAspectRatio="none" aria-hidden="true">
    <polygon points="0,0 487,0 482,14 0,14" fill="var(--slate-blue)"/>
    <polygon points="491,0 746,0 746,14 486,14" fill="var(--charcoal)"/>
  </svg>
</section>

<section class="card card--back" aria-label="Business card back">
  <div class="wordmark">
    <span class="wordmark__square"></span>
    <span class="wordmark__name">Velt<br>Commercial</span>
  </div>
</section>

</body>
</html>
```